Business Card design for insurance broker in Denver, CO, USA

I need a business card designed using this logo that was just created. We sell life and disability income insurance to US consumers.
Looking for a professionally designed card to make use of the logo and have something to hand to prospects or new business referral sources. The card could be white, gray, black or whatever you would recommend.

Target Market(s)

US Consumers and other financial professionals that I partner with.

Industry/Entity Type

Insurance Broker

Contact Information for Business Card

Owen T. Farrow, CLU, LUTCF (please note that CLU should have a superscript R in a circle for registered trademark)
President
phone (303) 555-0187
email owen@keelbrookcover.example
4620 W. Halvern Rd, Suite 300, Larkmoor Heights, CO 80999
Somewhere fit in a tagline saying "Your resource for life, long term care, and disability insurance" (maybe the back if it doesn't fit on the front, your call)

Font styles to use
Sans Serif

Requirements
Must have
• Must have logo in correct blue and gray colors, my name, address, phone, email. Order and placement determined by the designer.
• I just want something that looks a more professional than what I could have done using the business card designer tool on pixelbazaar.example or QuillPress, or any other do-it-yourself tool
• A regular rectangular business card with square corners is preferred
Nice to have
• I included the logos of 2 organizations I belong to (GKLS and WOBCE). They should be small, but visible on the back only. If it doesn’t look good, this is not a requirement, feel free to drop it.
Should not have
• Do not add any colors not already in the logo, except use of black and whites which are okay. If you use the logo on the back and want to make that in all black, gray or white, that may be okay as well.

```html
<!DOCTYPE html>
<html lang="en">
<head>
<meta charset="utf-8">
<title>Keelbrook Cover – Business Card</title>
<link href="https://fonts.googleapis.com/css2?family=Montserrat:wght@300;400;600&family=Open+Sans:wght@400&display=swap" rel="stylesheet">
<style>
  :root {
    --page: #161616;
    --card: #252525;
    --blue: #2a8fd8;
    --grey: #b9b9b9;
    --light: #d6d6d6;
  }
  * { margin: 0; padding: 0; box-sizing: border-box; }
  html, body { width: 1200px; height: 900px; overflow: hidden; background: var(--page); }
  .stage { position: relative; width: 1200px; height: 900px; }
  .card {
    position: absolute; left: 250px; width: 700px; height: 400px;
    background: var(--card); overflow: hidden;
    font-family: "Montserrat", sans-serif;
  }
  .card--front { top: 35px; }
  .card--back { top: 465px; }

  .brand__name {
    font-family: "Montserrat", sans-serif; font-weight: 600;
    color: var(--blue); letter-spacing: 1px; text-transform: uppercase;
    white-space: nowrap;
  }

  .front__brand { position: absolute; left: 0; right: 0; top: 150px; text-align: center; font-size: 36px; }
  .tagline {
    position: absolute; left: 0; right: 0; top: 300px; text-align: center;
    font-weight: 600; font-size: 12.5px; letter-spacing: 1px;
    color: var(--grey); text-transform: uppercase;
  }

  .back__brand { position: absolute; left: 48px; top: 150px; font-size: 23px; }
  .person { position: absolute; left: 375px; top: 128px; }
  .person__name {
    font-weight: 300; font-size: 25px; color: var(--light);
    text-transform: uppercase; letter-spacing: 0.5px; white-space: nowrap;
  }
  .person__name strong { font-weight: 600; }
  .person__creds { font-weight: 400; font-size: 18px; color: var(--blue); margin-top: 2px; }
  .person__creds sup { font-size: 10px; }
  .contact { list-style: none; margin-top: 22px; font-family: "Open Sans", sans-serif; font-size: 16px; color: var(--light); }
  .contact li { display: flex; align-items: center; gap: 12px; margin-bottom: 10px; white-space: nowrap; }
  .contact svg { width: 17px; height: 17px; fill: var(--blue); flex: none; }
  .address {
    position: absolute; left: 48px; top: 322px; display: flex; align-items: center; gap: 10px;
    font-family: "Open Sans", sans-serif; font-size: 16.5px; color: var(--light); white-space: nowrap;
  }
  .address svg { width: 14px; height: 18px; fill: var(--blue); flex: none; }
</style>
</head>
<body>
<main class="stage">

  <section class="card card--front">
    <p class="brand__name front__brand">Keelbrook Cover</p>
    <p class="tagline">Your resource for life, long term care, and disability insurance</p>
  </section>

  <section class="card card--back">
    <p class="brand__name back__brand">Keelbrook Cover</p>

    <div class="person">
      <h1 class="person__name">Owen T. <strong>Farrow</strong></h1>
      <p class="person__creds">CLU<sup>®</sup>, LUTCF</p>
      <ul class="contact">
        <li>
          <svg viewBox="0 0 24 24" aria-hidden="true"><path d="M3 9c0-3 4-5 9-5s9 2 9 5v2h-5V9c-1-.6-2.4-1-4-1s-3 .4-4 1v2H3zM6 12h12l2 8H4z"/></svg>
          (303) 555-0187
        </li>
        <li>
          <svg viewBox="0 0 24 24" aria-hidden="true"><path d="M2 5h20v14H2zM4 7v.5l8 5.5 8-5.5V7z" fill-rule="evenodd"/></svg>
          owen@keelbrookcover.example
        </li>
      </ul>
    </div>

    <p class="address">
      <svg viewBox="0 0 14 18" aria-hidden="true"><path d="M7 0a7 7 0 0 0-7 7c0 5 7 11 7 11s7-6 7-11a7 7 0 0 0-7-7zm0 9.5A2.5 2.5 0 1 1 7 4.5a2.5 2.5 0 0 1 0 5z"/></svg>
      4620 W. Halvern Rd, Suite 300, Larkmoor Heights, CO 80999
    </p>
  </section>

</main>
</body>
</html>
```